Copperleaf Roofing Business Card

This is my current business card. But I’d like to make some changes. Somewhere on the card I’d like to list some of the services we offer. Maybe on the back? But I’d still like to keep the red. White and black modern look.

-residential & commercial roofing
-Roof Repairs & Maintenance
-Storm Damage & Insurance Claims specialist
-Christmas Lights and permanent Christmas lights
Fencing. Windows. Gutters. Siding. Sheetrock, painting.

```html
<!DOCTYPE html>
<html lang="en">
<head>
<meta charset="utf-8">
<title>Copperleaf Roofing Co. — Business Card</title>
<link href="https://fonts.googleapis.com/css2?family=Michroma&family=Montserrat:wght@400;500&display=swap" rel="stylesheet">
<style>
  :root {
    --bg: #1d1d1d;
    --card-black: #050505;
    --red: #d0202a;
    --red-deep: #7a0f14;
    --red-mid: #a8151c;
    --white: #f2f2f2;
    --grey: #cfcfcf;
  }
  * { box-sizing: border-box; margin: 0; padding: 0; }
  html, body {
    width: 1200px; height: 955px; overflow: hidden;
    background: var(--bg);
  }
  .canvas { position: relative; width: 1200px; height: 955px; }

  .card {
    position: absolute; left: 334px; width: 551px; height: 315px;
    overflow: hidden;
  }
  .card--front { top: 141px; }
  .card--back { top: 513px; background: var(--card-black); }

  .plaid {
    position: absolute; inset: 0;
    background: linear-gradient(135deg, var(--red-mid) 0%, var(--red) 35%, var(--red-deep) 70%, var(--red-mid) 100%);
  }
  .plaid-strip {
    position: absolute; left: 0; right: 0; bottom: 0; height: 9px;
    background: linear-gradient(90deg, var(--red-deep), var(--red), var(--red-deep), var(--red));
  }

  .emblem { position: absolute; border-radius: 50%; }
  .card--front .emblem {
    left: 207px; top: 44px; width: 138px; height: 138px;
    background: var(--red); border: 3px solid var(--white);
  }
  .card--back .emblem {
    left: 237px; top: 19px; width: 76px; height: 76px;
    background: var(--red); border: 2px solid var(--white);
  }

  .brand {
    position: absolute; left: 0; right: 0; text-align: center;
    font-family: "Michroma", sans-serif; font-weight: 400;
    color: var(--white); line-height: 1;
  }
  .card--front .brand-name { top: 202px; font-size: 29px; }
  .card--front .brand-sub { top: 244px; font-size: 20px; }
  .card--back .brand-name { top: 106px; font-size: 18px; }
  .card--back .brand-sub { top: 129px; font-size: 12px; }

  .person {
    position: absolute; right: 310px; top: 184px; text-align: right;
    font-family: "Michroma", sans-serif;
  }
  .person-name { font-size: 14px; color: var(--white); letter-spacing: 2px; line-height: 1; }
  .person-name .surname { color: var(--red); }
  .person-role {
    font-family: "Montserrat", sans-serif; font-size: 11px; letter-spacing: 1.5px;
    color: var(--red); margin-top: 4px;
  }

  .divider { position: absolute; left: 258px; width: 1.5px; background: var(--red); }
  .divider--contact { top: 173px; height: 53px; }
  .divider--services { top: 244px; height: 23px; }

  .contact { position: absolute; left: 280px; top: 166px; list-style: none; }
  .contact li {
    display: flex; align-items: center; gap: 9px; height: 21px;
    font-family: "Montserrat", sans-serif; font-size: 12.5px; color: var(--white); letter-spacing: 0.6px;
  }
  .contact svg { width: 10px; height: 10px; flex: none; }

  .services {
    position: absolute; top: 247px; font-family: "Montserrat", sans-serif;
    font-size: 8px; color: var(--grey); letter-spacing: 0.3px; line-height: 16.5px; list-style: none;
  }
  .services--left { right: 310px; text-align: right; }
  .services--right { left: 275px; }
  .services-extra {
    position: absolute; left: 0; right: 0; top: 280px; text-align: center;
    font-family: "Montserrat", sans-serif; font-size: 8px; color: var(--grey); letter-spacing: 0.3px;
  }
</style>
</head>
<body>
<main class="canvas">

  <section class="card card--front" aria-label="Card front">
    <div class="plaid" role="img" aria-label="Red, black and white tartan plaid pattern"></div>
    <div class="emblem" aria-hidden="true"></div>
    <p class="brand brand-name">COPPERLEAF</p>
    <p class="brand brand-sub">ROOFING CO.</p>
  </section>

  <section class="card card--back" aria-label="Card back">
    <div class="emblem" aria-hidden="true"></div>
    <p class="brand brand-name">COPPERLEAF</p>
    <p class="brand brand-sub">ROOFING CO.</p>

    <div class="person">
      <p class="person-name">EWAN <span class="surname">CARLISLE</span></p>
      <p class="person-role">Owner</p>
    </div>
    <div class="divider divider--contact"></div>

    <ul class="contact">
      <li>
        <svg viewBox="0 0 24 24"><path fill="#d0202a" d="M6.6 10.8a15.1 15.1 0 0 0 6.6 6.6l2.2-2.2a1 1 0 0 1 1-.25 11.4 11.4 0 0 0 3.6.57 1 1 0 0 1 1 1V20a1 1 0 0 1-1 1A17 17 0 0 1 3 4a1 1 0 0 1 1-1h3.5a1 1 0 0 1 1 1c0 1.25.2 2.45.57 3.57a1 1 0 0 1-.25 1z"/></svg>
        682-555-0148
      </li>
      <li>
        <svg viewBox="0 0 24 24"><rect x="2" y="5" width="20" height="14" fill="#d0202a"/><path d="M2 5l10 8 10-8" stroke="#050505" stroke-width="2" fill="none"/></svg>
        ewan@copperleafroofing.co
      </li>
      <li>
        <svg viewBox="0 0 24 24" fill="none" stroke="#d0202a" stroke-width="2"><circle cx="12" cy="12" r="9"/><path d="M3 12h18M12 3c3 3 3 15 0 18M12 3c-3 3-3 15 0 18"/></svg>
        www.copperleafroofing.co
      </li>
    </ul>

    <ul class="services services--left">
      <li>RESIDENTIAL &amp; COMMERCIAL ROOFING</li>
      <li>STORM DAMAGE &amp; INSURANCE CLAIMS SPECIALIST</li>
    </ul>
    <div class="divider divider--services"></div>
    <ul class="services services--right">
      <li>ROOF REPAIRS &amp; MAINTENANCE</li>
      <li>CHRISTMAS LIGHTS AND PERMANENT CHRISTMAS LIGHT</li>
    </ul>
    <p class="services-extra">FENCING. WINDOWS. GUTTERS. SIDING. SHEETROCK, PAINTING</p>

    <div class="plaid-strip" role="img" aria-label="Thin band of red tartan plaid pattern"></div>
  </section>

</main>
</body>
</html>
```